Concierge Dental / Medical Supply Ordering Business - Sleek, Efficient, Professional, Elite

www.brantonkeelmedical.com - example website.

We are a concierge supply ordering business for medical and dental that provide DSO price savings on supplies while maintaining business autonomy and independence.

We want a very simple website that looks very professional says what we do and gives a very simple method to contact us & sign up as above.

Target Market(s)

Independent Dental and Medical Practices

Industry/Entity Type

Dental and Medical - healthcare

Coding

Coded - Design and coding required

Number of Pages Required

3 page

Font styles to use
Sans Serif

Colors
0054AA
0677BA
7BADD7
CADEEF
E8F1F8

Requirements
Must have
• Simple contact page, sleek efficient design, uncomplicated.
Nice to have
• Sign up page vs just a contact page.
Should not have
• Lots of pages, hard to navigate,

```html
<!DOCTYPE html>
<html lang="en">
<head>
<meta charset="utf-8">
<title>Branton Keel Supply — Medical Supply Ordering</title>
<link href="https://fonts.googleapis.com/css2?family=Open+Sans:wght@400;600;700;800&display=swap" rel="stylesheet">
<style>
:root{
  --accent:#14a3d0;
  --accent-dark:#0677BA;
  --brand:#0054AA;
  --navy:#0c1f3f;
  --ink:#111827;
  --text:#5b6472;
  --muted:#8a93a0;
  --light:#f3f4f6;
  --pale:#E8F1F8;
  --sky:#CADEEF;
  --footer:#0b0b0d;
  --white:#ffffff;
}
*{box-sizing:border-box;margin:0;padding:0}
html,body{width:1200px;height:4692px;overflow:hidden}
body{font-family:"Open Sans",Arial,sans-serif;color:var(--ink);background:var(--white);position:relative}
.abs{position:absolute}
section,header,footer{position:absolute;left:0;width:1200px}
.eyebrow{font-size:13px;font-weight:700;letter-spacing:1px;color:var(--accent);text-transform:uppercase}
.btn{display:inline-flex;align-items:center;gap:10px;background:var(--accent);color:var(--white);font-weight:700;font-size:15px;padding:12px 24px;border-radius:4px}
.btn svg{width:16px;height:16px}
.center{left:0;width:1200px;text-align:center}

/* hero */
.hero{top:0;height:860px;background:linear-gradient(160deg,#2b3a4c 0%,#1a2330 45%,#2e3440 100%)}
.hero-photo{position:absolute;inset:0;background:radial-gradient(ellipse at 30% 60%,rgba(120,140,160,.35),transparent 60%),radial-gradient(ellipse at 75% 40%,rgba(90,110,130,.35),transparent 55%)}
.topbar{top:0;height:40px;left:0;width:1200px;background:rgba(0,0,0,.35);font-size:12px;color:#cfd6de}
.topbar .item{position:absolute;top:12px;display:flex;gap:6px;align-items:center}
.topbar .soc{position:absolute;top:13px;width:14px;height:14px;background:#cfd6de;border-radius:2px}
.logo{display:flex;align-items:center;gap:10px;color:var(--white);font-weight:700;font-size:15px}
.logo .mark{width:48px;height:48px;background:var(--accent);border-radius:6px}
.badge{position:absolute;top:56px;display:flex;align-items:center;gap:10px;color:var(--white);font-size:13px;font-weight:700;line-height:1.25}
.badge .ic{width:42px;height:42px;border:2px solid var(--accent);border-radius:50%;display:flex;align-items:center;justify-content:center}
.nav{top:126px;left:112px;width:1028px;height:58px;background:var(--white);border-radius:4px;display:flex;align-items:center;padding:0 18px;font-size:15px;font-weight:600;color:var(--ink)}
.nav a{padding:0 42px;height:58px;display:flex;align-items:center;text-decoration:none;color:inherit}
.nav a.active{background:var(--pale);border-bottom:3px solid var(--accent)}
.nav .btn{margin-left:auto;padding:10px 20px;font-size:14px}
.hero h1{top:390px;font-size:64px;font-weight:700;line-height:1.15;color:var(--white)}
.hero .eyebrow{top:336px;color:#cfd6de;font-weight:600}
.hero .btn{top:612px;left:548px}
.hero-wave{position:absolute;left:0;top:680px;width:1200px;height:180px}

/* about */
.about{top:860px;height:580px}
.about-photo{left:100px;top:80px;width:440px;height:440px;border-radius:50%;border:10px solid var(--white);box-shadow:0 8px 30px rgba(0,0,0,.15);background:linear-gradient(135deg,#7a8da0,#c7b39a 50%,#3e4b5c)}
.about-badge{left:430px;top:420px;width:80px;height:80px;border-radius:50%;background:var(--white);box-shadow:0 4px 14px rgba(0,0,0,.2);display:flex;align-items:center;justify-content:center}
.about-badge span{width:40px;height:40px;background:var(--navy);border-radius:6px}
.about-copy{left:612px;top:96px;width:520px}
.about-copy h2{font-size:40px;line-height:1.2;color:var(--navy);font-weight:700;margin:14px 0 22px}
.about-copy h3{font-size:20px;color:var(--navy);font-weight:700;margin-bottom:18px}
.about-copy p{font-size:14px;color:var(--text);line-height:1.7;margin-bottom:18px}

/* services */
.services{top:1440px;height:540px;background:var(--light)}
.services .eyebrow{top:44px}
.section-title{font-size:44px;font-weight:700;color:var(--navy)}
.services .section-title{top:64px}
.card{position:absolute;top:186px;width:316px;height:316px;background:var(--white);border-bottom:4px solid var(--accent);text-align:center;padding:60px 36px 0;box-shadow:0 4px 16px rgba(0,0,0,.05)}
.card h4{font-size:20px;font-weight:600;color:var(--ink);margin:22px 0 14px}
.card p{font-size:14px;color:var(--text);line-height:1.6}
.card.feature{background:linear-gradient(160deg,#4a5566,#1e2633);color:var(--white);padding-top:204px;text-align:center}
.card.feature h4,.card.feature p{color:var(--white)}
.card.feature h4{margin-top:0}

/* cta */
.cta{top:1980px;height:400px;background:linear-gradient(180deg,#2a2f38,#1a1e25 60%,#2c313a)}
.cta h2{top:120px;font-size:32px;font-weight:700;color:var(--white);line-height:1.4}
.cta h2 em{font-style:normal;color:var(--accent)}
.contact-pill{left:352px;top:292px;width:496px;height:44px;background:var(--white);border-radius:4px;display:flex;align-items:center;justify-content:center;gap:26px;font-size:15px;font-weight:600;color:var(--ink)}
.contact-pill .sep{width:1px;height:22px;background:#c8ccd2}
.contact-pill span{display:flex;align-items:center;gap:8px}

/* why */
.why{top:2380px;height:580px;background:#f5f6f8}
.why .eyebrow{top:40px}
.why .section-title{top:62px}
.feat{position:absolute;width:280px;font-size:14px;color:var(--text);line-height:1.5}
.feat h5{font-size:17px;font-weight:700;color:var(--ink);margin-bottom:6px}
.feat.left{left:100px;text-align:right}
.feat.right{left:828px}
.why-art{left:420px;top:170px;width:360px;height:360px}

/* testimonials */
.testi{top:2960px;height:620px;background:linear-gradient(180deg,#1c2029,#14171d)}
.testi .eyebrow{top:56px;color:#cfd6de;font-weight:600}
.testi .section-title{top:78px;color:var(--white);font-size:42px}
.tcard{position:absolute;top:200px;width:322px;height:290px;background:var(--navy);border-bottom:5px solid var(--accent);text-align:center;padding:78px 28px 0;color:#cbd3de}
.tcard.light{background:var(--white);color:var(--text)}
.tcard .avatar{position:absolute;left:126px;top:-36px;width:70px;height:70px;border-radius:50%;border:4px solid var(--white);background:linear-gradient(135deg,#8a98a8,#4d5b6b)}
.tcard h6{font-size:17px;font-weight:700;color:var(--white);margin-bottom:6px}
.tcard.light h6{color:var(--ink)}
.stars{color:#f2b400;font-size:16px;letter-spacing:3px;margin-bottom:16px}
.tcard p{font-size:14px;line-height:1.6}
.tcard .quote{position:absolute;left:0;width:100%;bottom:20px;font-size:48px;font-weight:800;color:var(--accent);line-height:1}
.dots{top:540px;left:576px;display:flex;gap:8px}
.dots span{width:10px;height:10px;border-radius:50%;background:#5a606b}
.dots span.on{background:var(--white);width:22px;border-radius:5px}

/* contact */
.contact{top:3580px;height:620px}
.contact h2{left:110px;top:76px;font-size:44px;font-weight:700;color:var(--ink)}
.contact h2 span{font-weight:400}
.cinfo{position:absolute;left:110px;display:flex;gap:18px;align-items:center}
.cinfo .ic{width:56px;height:56px;border-radius:50%;background:var(--pale);display:flex;align-items:center;justify-content:center}
.cinfo b{display:block;font-size:13px;font-weight:700;color:var(--ink);letter-spacing:.5px}
.cinfo small{font-size:13px;color:var(--muted)}
.form{left:600px;top:60px;width:500px;height:540px;background:var(--white);border-top:5px solid var(--accent);box-shadow:0 10px 40px rgba(0,0,0,.12);padding:32px 40px;z-index:3}
.form h3{font-size:24px;font-weight:600;color:var(--ink);margin-bottom:36px}
.form label{display:block;font-size:13px;font-weight:700;color:var(--ink);margin-bottom:8px}
.field{height:42px;border:1px solid #d5d9de;border-radius:22px;font-size:13px;color:#9aa1ab;padding:12px 18px;margin-bottom:22px}
.form .row{display:flex;gap:20px}
.form .row>div{flex:1}
.field.area{height:120px;border-radius:8px}

/* footer */
.footer{top:4160px;height:532px;background:var(--footer);color:#b6bcc4;font-size:13px}
.footer-wave{position:absolute;left:0;top:-70px;width:1200px;height:190px}
.fcol{position:absolute;top:140px}
.fcol h6{color:var(--white);font-size:15px;font-weight:700;margin-bottom:18px}
.fcol li{list-style:none;margin-bottom:7px}
.flogo{left:110px;top:110px}
.flogo p{width:300px;line-height:1.6;margin:16px 0}
.fsoc{display:flex;gap:8px}
.fsoc span{width:26px;height:26px;background:var(--accent);border-radius:3px}
.nl-input{display:flex;margin-top:16px}
.nl-input div{width:200px;height:40px;background:var(--white);color:#9aa1ab;padding:11px 14px;font-size:13px}
.nl-input span{width:44px;height:40px;background:var(--accent);display:flex;align-items:center;justify-content:center}
.frow{position:absolute;left:110px;top:376px;width:980px;display:flex;justify-content:space-between;border-top:1px solid #23262c;padding-top:22px}
.frow>div{display:flex;gap:12px;align-items:center}
.frow .ic{width:44px;height:44px;border-radius:50%;background:#1f2229;display:flex;align-items:center;justify-content:center}
.frow b{display:block;color:var(--white);font-size:14px}
.copyright{top:494px;font-size:12px;color:#8a909a;letter-spacing:1px}
</style>
</head>
<body>

<header class="hero">
  <div class="hero-photo" role="img" aria-label="Photo of a medical team at work in an office"></div>
  <div class="topbar abs">
    <div class="item" style="left:112px">(+1) 555-014-220</div>
    <div class="item" style="left:260px">hello@brantonkeelmedical.com</div>
    <div class="item" style="left:480px">120 Keel Street</div>
    <span class="soc" style="left:1060px"></span><span class="soc" style="left:1082px"></span><span class="soc" style="left:1104px"></span><span class="soc" style="left:1126px"></span>
  </div>
  <div class="logo abs" style="left:112px;top:52px"><span class="mark"></span>Branton Keel Supply</div>
  <div class="badge" style="left:830px"><span class="ic"><svg width="20" height="20" viewBox="0 0 24 24" fill="none" stroke="#14a3d0" stroke-width="2"><circle cx="12" cy="12" r="9"/><path d="M12 7v5l3 3"/></svg></span>24/7<br>Service</div>
  <div class="badge" style="left:980px"><span class="ic"><svg width="20" height="20" viewBox="0 0 24 24" fill="none" stroke="#14a3d0" stroke-width="2"><circle cx="12" cy="8" r="4"/><path d="M4 21c1-5 15-5 16 0"/></svg></span>Qualified<br>Professionals</div>
  <nav class="nav abs">
    <a class="active">Home</a><a>About Us</a><a>Services</a><a>Blog</a><a>Contact</a>
    <span class="btn">Get A Quote</span>
  </nav>
  <div class="eyebrow abs center">Medical Supply Ordering</div>
  <h1 class="abs center">Where Efficiency<br>Meets Profitability.</h1>
  <span class="btn abs">About Us</span>
  <svg class="hero-wave" viewBox="0 0 1200 180" preserveAspectRatio="none">
    <path d="M0 60 C300 170 700 170 1200 20 L1200 180 L0 180Z" fill="#0c1f3f"/>
    <path d="M0 90 C320 190 720 180 1200 40 L1200 180 L0 180Z" fill="#14a3d0"/>
    <path d="M0 110 C340 200 760 190 1200 70 L1200 180 L0 180Z" fill="#ffffff"/>
  </svg>
</header>

<section class="about">
  <div class="about-photo abs" role="img" aria-label="Photo of two professionals reviewing a tablet"></div>
  <div class="about-badge abs"><span></span></div>
  <div class="about-copy abs">
    <div class="eyebrow">Who We Are</div>
    <h2>The team you can trust<br>to get the job done</h2>
    <h3>Supply Ordering Solutions for Medical Success.</h3>
    <p>Lorem ipsum dolor sit amet, consectetur adipiscing elit, sed do eiusmod tempor incididunt ut labore et dolore magna aliqua. Ut enim ad minim veniam, quis nostrud exercitation ullamco laboris nisi ut aliquip.</p>
    <p>Lorem ipsum dolor sit amet, consectetur adipiscing elit, sed do eiusmod tempor incididunt ut labore et dolore magna aliqua.</p>
    <span class="btn">Contact us <svg viewBox="0 0 24 24" fill="none" stroke="#fff" stroke-width="2.5"><path d="M4 12h15M13 6l6 6-6 6"/></svg></span>
  </div>
</section>

<section class="services">
  <div class="eyebrow abs center">Our Services</div>
  <h2 class="section-title abs center">Services We Offer</h2>
  <div class="card feature" style="left:92px" role="img" aria-label="Photo of a smiling customer service professional">
    <h4>Order Fulfillment</h4>
    <p>Lorem ipsum dolor sit amet, consectetur adipiscing elit, sed do eiusmod tempor</p>
  </div>
  <div class="card" style="left:442px">
    <svg width="48" height="48" viewBox="0 0 24 24" fill="none" stroke="#14a3d0" stroke-width="1.5"><circle cx="12" cy="12" r="9"/><path d="M14.5 9c-.5-1-1.5-1.5-2.5-1.5-1.5 0-2.5.8-2.5 2s1 1.7 2.5 2 2.5.8 2.5 2-1 2-2.5 2c-1 0-2-.5-2.5-1.5M12 6v1.5M12 16.5V18"/></svg>
    <h4>Price Savings</h4>
    <p>Lorem ipsum dolor sit amet, consectetur adipiscing elit, sed do eiusmod tempor</p>
  </div>
  <div class="card" style="left:792px">
    <svg width="48" height="48" viewBox="0 0 24 24" fill="none" stroke="#14a3d0" stroke-width="1.5"><path d="M12 3l2.7 5.6 6.1.8-4.4 4.2 1.1 6.1L12 16.8l-5.5 2.9 1.1-6.1-4.4-4.2 6.1-.8z"/></svg>
    <h4>Timely Delivery</h4>
    <p>Lorem ipsum dolor sit amet, consectetur adipiscing elit, sed do eiusmod tempor</p>
  </div>
</section>

<section class="cta" role="img" aria-label="Photo of a busy office team in the background">
  <h2 class="abs center">We’re On <em>Call 24/7</em> to React Promptly to Your<br>Medical Supply Ordering Needs</h2>
  <div class="contact-pill abs">
    <span><svg width="16" height="16" viewBox="0 0 24 24" fill="#0c1f3f"><path d="M6.6 10.8a15 15 0 006.6 6.6l2.2-2.2c.3-.3.7-.4 1-.2 1.1.4 2.3.6 3.6.6.6 0 1 .4 1 1V20c0 .6-.4 1-1 1A17 17 0 013 4c0-.6.4-1 1-1h3.5c.6 0 1 .4 1 1 0 1.3.2 2.5.6 3.6.1.3 0 .7-.2 1z"/></svg>(+1) 555-014-220</span>
    <i class="sep"></i>
    <span><svg width="16" height="16" viewBox="0 0 24 24" fill="none" stroke="#0c1f3f" stroke-width="2"><rect x="3" y="5" width="18" height="14" rx="2"/><path d="M3 7l9 6 9-6"/></svg>hello@brantonkeelmedical.com</span>
  </div>
</section>

<section class="why">
  <div class="eyebrow abs center">Why Choose Us</div>
  <h2 class="section-title abs center">Why Choose Us</h2>
  <div class="feat left" style="top:210px"><h5>Expertise &amp; Experience</h5>Lorem ipsum dolor sit amet, consectetur adipiscing elit</div>
  <div class="feat left" style="top:330px"><h5>Research Capabilities</h5>Lorem ipsum dolor sit amet, consectetur adipiscing elit</div>
  <div class="feat left" style="top:450px"><h5>Quality Assurance</h5>Lorem ipsum dolor sit amet, consectetur adipiscing elit</div>
  <div class="feat right" style="top:210px"><h5>Customization</h5>Lorem ipsum dolor sit amet, consectetur adipiscing elit</div>
  <div class="feat right" style="top:330px"><h5>Cost-Effective</h5>Lorem ipsum dolor sit amet, consectetur adipiscing elit</div>
  <div class="feat right" style="top:450px"><h5>Client-Centric</h5>Lorem ipsum dolor sit amet, consectetur adipiscing elit</div>
  <svg class="why-art abs" viewBox="0 0 360 360">
    <circle cx="180" cy="180" r="130" fill="none" stroke="#0c1f3f" stroke-width="2"/>
    <circle cx="180" cy="180" r="92" fill="#ffffff" stroke="#CADEEF" stroke-width="6"/>
    <rect x="130" y="130" width="100" height="100" rx="12" fill="#0c1f3f"/>
    <g fill="#ffffff" stroke="#0c1f3f" stroke-width="2">
      <circle cx="115" cy="67" r="22"/><circle cx="245" cy="67" r="22"/>
      <circle cx="50" cy="180" r="22"/><circle cx="310" cy="180" r="22"/>
      <circle cx="115" cy="293" r="22"/><circle cx="245" cy="293" r="22"/>
    </g>
    <g fill="none" stroke="#14a3d0" stroke-width="2">
      <path d="M107 67l6 6 10-12"/><path d="M237 67l6 6 10-12"/>
      <path d="M42 180l6 6 10-12"/><path d="M302 180l6 6 10-12"/>
      <path d="M107 293l6 6 10-12"/><path d="M237 293l6 6 10-12"/>
    </g>
  </svg>
</section>

<section class="testi">
  <div class="eyebrow abs center">Testimonials</div>
  <h2 class="section-title abs center">What Clients are saying</h2>
  <div class="tcard light" style="left:95px">
    <span class="avatar" role="img" aria-label="Client portrait"></span>
    <h6>Marcus Hale</h6><div class="stars">★★★★★</div>
    <p>Lorem ipsum dolor sit amet, consectetur adipiscing elit, sed do eiusmod tempor incididunt ut labore et dolore magna aliqua.</p>
    <div class="quote">“</div>
  </div>
  <div class="tcard" style="left:439px">
    <span class="avatar" role="img" aria-label="Client portrait"></span>
    <h6>Lena Corwin</h6><div class="stars">★★★★★</div>
    <p>Lorem ipsum dolor sit amet, consectetur adipiscing elit, sed do eiusmod tempor incididunt ut labore et dolore magna aliqua.</p>
    <div class="quote">“</div>
  </div>
  <div class="tcard" style="left:783px">
    <span class="avatar" role="img" aria-label="Client portrait"></span>
    <h6>Reid Talbot</h6><div class="stars">★★★★★</div>
    <p>Lorem ipsum dolor sit amet, consectetur adipiscing elit, sed do eiusmod tempor incididunt ut labore et dolore magna aliqua.</p>
    <div class="quote">“</div>
  </div>
  <div class="dots abs"><span class="on"></span><span></span></div>
</section>

<section class="contact">
  <h2 class="abs">Contact Us <span>Today</span></h2>
  <div class="cinfo" style="top:180px"><span class="ic"><svg width="22" height="22" viewBox="0 0 24 24" fill="#14a3d0"><path d="M12 2a7 7 0 00-7 7c0 5 7 13 7 13s7-8 7-13a7 7 0 00-7-7zm0 9.5A2.5 2.5 0 1112 6.5a2.5 2.5 0 010 5z"/></svg></span><div><b>HEAD OFFICE</b><small>120 Keel Street, Suite 4</small></div></div>
  <div class="cinfo" style="top:270px"><span class="ic"><svg width="22" height="22" viewBox="0 0 24 24" fill="none" stroke="#14a3d0" stroke-width="2"><rect x="3" y="5" width="18" height="14" rx="2"/><path d="M3 7l9 6 9-6"/></svg></span><div><b>EMAIL ADDRESS</b><small>hello@brantonkeelmedical.com</small></div></div>
  <div class="cinfo" style="top:360px"><span class="ic"><svg width="22" height="22" viewBox="0 0 24 24" fill="#14a3d0"><path d="M6.6 10.8a15 15 0 006.6 6.6l2.2-2.2c.3-.3.7-.4 1-.2 1.1.4 2.3.6 3.6.6.6 0 1 .4 1 1V20c0 .6-.4 1-1 1A17 17 0 013 4c0-.6.4-1 1-1h3.5c.6 0 1 .4 1 1 0 1.3.2 2.5.6 3.6.1.3 0 .7-.2 1z"/></svg></span><div><b>CALL US NOW</b><small>Call Now: (+1) 555-014-220</small></div></div>
  <div class="form abs">
    <h3>Send Us A Message</h3>
    <div class="row">
      <div><label>First Name</label><div class="field">John</div></div>
      <div><label>Last Name</label><div class="field">Doe</div></div>
    </div>
    <label>Email</label><div class="field">info@example.com</div>
    <label>Message</label><div class="field area">Type Your Message</div>
    <span class="btn">Contact us <svg viewBox="0 0 24 24" fill="none" stroke="#fff" stroke-width="2.5"><path d="M4 12h15M13 6l6 6-6 6"/></svg></span>
  </div>
</section>

<footer class="footer">
  <svg class="footer-wave" viewBox="0 0 1200 190" preserveAspectRatio="none">
    <path d="M0 150 C250 20 500 0 1200 150 L1200 190 L0 190Z" fill="#14a3d0"/>
    <path d="M0 165 C260 50 520 30 1200 165 L1200 190 L0 190Z" fill="#0c1f3f"/>
    <path d="M0 180 C270 80 540 60 1200 180 L1200 190 L0 190Z" fill="#0b0b0d"/>
  </svg>
  <div class="fcol flogo">
    <div class="logo"><span class="mark"></span>Branton Keel Supply</div>
    <p>Lorem ipsum dolor sit amet, consectetur adipiscing elit, sed do eiusmod tempor incididunt ut labore et dolore.</p>
    <div class="fsoc"><span></span><span></span><span></span><span></span></div>
  </div>
  <div class="fcol" style="left:490px"><h6>Quick Links</h6><ul><li>Home</li><li>Services</li><li>About Us</li><li>Contact</li><li>Blog</li><li>Testimonials</li></ul></div>
  <div class="fcol" style="left:660px;top:178px"><ul><li>Cookies Policy</li><li>Terms of Use</li><li>Careers</li><li>Our Team</li><li>News</li></ul></div>
  <div class="fcol" style="left:830px"><h6>Newsletter</h6><p style="width:260px;line-height:1.6">Lorem ipsum dolor sit amet, consectetur adipiscing elit sed do.</p>
    <div class="nl-input"><div>Enter Email Address</div><span><svg width="16" height="16" viewBox="0 0 24 24" fill="#fff"><path d="M8 5l8 7-8 7z"/></svg></span></div>
  </div>
  <div class="frow">
    <div><span class="ic"><svg width="18" height="18" viewBox="0 0 24 24" fill="#14a3d0"><path d="M12 2a7 7 0 00-7 7c0 5 7 13 7 13s7-8 7-13a7 7 0 00-7-7z"/></svg></span><div><b>Address</b>120 Keel Street</div></div>
    <div><span class="ic"><svg width="18" height="18" viewBox="0 0 24 24" fill="none" stroke="#14a3d0" stroke-width="2"><rect x="3" y="5" width="18" height="14" rx="2"/><path d="M3 7l9 6 9-6"/></svg></span><div><b>Email Us</b>hello@brantonkeelmedical.com</div></div>
    <div><span class="ic"><svg width="18" height="18" viewBox="0 0 24 24" fill="#14a3d0"><path d="M6.6 10.8a15 15 0 006.6 6.6l2.2-2.2c.3-.3.7-.4 1-.2 1.1.4 2.3.6 3.6.6.6 0 1 .4 1 1V20c0 .6-.4 1-1 1A17 17 0 013 4c0-.6.4-1 1-1h3.5c.6 0 1 .4 1 1 0 1.3.2 2.5.6 3.6.1.3 0 .7-.2 1z"/></svg></span><div><b>Contact Us</b>(+1) 555-014-220</div></div>
    <div><span class="ic"><svg width="18" height="18" viewBox="0 0 24 24" fill="none" stroke="#14a3d0" stroke-width="2"><circle cx="12" cy="12" r="9"/><path d="M12 7v5l3 3"/></svg></span><div><b>Opening Hour</b>Mon - Friday: 9am - 6pm</div></div>
  </div>
  <div class="copyright abs center">BRANTON KEEL SUPPLY</div>
</footer>

</body>
</html>
```